Help design website for "Brightwater Civic Advisors" to advance the common good

Here is the Google doc link that lays out the design:

https://files.plumrivet.example/sheet/d/7QmTzR2wLx9KpVbN4hJcY8sEaUoFdG3iXkMnPq5rWt6/edit?usp=sharing

Here is the Google drive folder with the logos and photos: https://vault.plumrivet.example/open?id=4HkWp9LzQe2TxRvN8mBaYc3DsUoJfG6

The testimonials are being gathered and will be shared by Friday, 1/4.

The winner will also have to migrate the coding files to my hosting site.

Thank you for your help! Looking forward to seeing your designs.

Target Market(s)

Prospective clients

Industry/Entity Type

Non Profit

Coding

Coded - Design and coding required

Number of Pages Required

5+ page

Requirements
Must have
• Noted in the Google doc regarding layout.
Nice to have

```html
<!DOCTYPE html>
<html lang="en">
<head>
<meta charset="utf-8">
<title>Brightwater Civic Advisors</title>
<link href="https://fonts.googleapis.com/css2?family=Montserrat:wght@300;400;500;600&family=Arimo:wght@400;700&display=swap" rel="stylesheet">
<style>
:root{
  --blue:#3a86cf;
  --blue-dark:#2f74b8;
  --ink:#2b2b2b;
  --text:#555;
  --grey-bg:#efefef;
  --footer:#262a33;
  --white:#fff;
  --line:#dcdcdc;
}
*{box-sizing:border-box;margin:0;padding:0}
html,body{width:1200px;height:3711px;overflow:hidden}
body{position:relative;background:var(--white);font-family:"Arimo",Arial,sans-serif;color:var(--text)}
.abs{position:absolute}
.h-section{font-family:"Montserrat",sans-serif;font-weight:300;font-size:36px;color:var(--ink);text-align:center;letter-spacing:1px;text-transform:uppercase}
.underline{height:3px;width:76px;background:var(--blue)}
.btn-outline{border:2px solid var(--blue);border-radius:30px;color:var(--blue);font-family:"Montserrat",sans-serif;font-size:13px;font-weight:500;text-align:center;text-transform:uppercase;background:var(--white)}
.btn-solid{background:var(--blue);border-radius:30px;color:var(--white);font-family:"Montserrat",sans-serif;font-weight:600;text-align:center;text-transform:uppercase}

/* nav */
.topline{left:0;top:0;width:1200px;height:4px;background:var(--blue)}
.nav{left:0;top:4px;width:1200px;height:102px}
.nav-links{left:110px;top:50px;display:flex;gap:46px;font-family:"Montserrat",sans-serif;font-size:13px;font-weight:600;color:var(--ink)}
.nav-links .active{color:var(--blue)}
.brand{left:860px;top:26px;display:flex;align-items:center;gap:14px}
.brand-mark{width:48px;height:48px;background:var(--blue)}
.brand-name{font-family:"Montserrat",sans-serif;font-weight:500;font-size:15px;letter-spacing:3px;line-height:19px;color:var(--ink);text-transform:uppercase}

/* hero */
.hero{left:0;top:106px;width:1200px;height:567px;background:linear-gradient(160deg,#4a4642 0%,#2c2a2b 45%,#6b5a55 75%,#3a3434 100%)}
.hero-title{left:413px;top:230px;width:391px;height:50px;background:var(--blue);color:var(--white);font-family:"Montserrat",sans-serif;font-weight:500;font-size:20px;letter-spacing:1px;display:flex;align-items:center;justify-content:center}
.hero-sub{left:331px;top:297px;width:560px;height:37px;background:rgba(20,20,20,.85);color:var(--white);font-family:"Montserrat",sans-serif;font-weight:500;font-size:13px;display:flex;align-items:center;justify-content:center;letter-spacing:.5px}

/* about */
.about-frame{left:186px;top:768px;width:376px;height:434px;border:2px solid #9cc3e8}
.about-photo-wrap{left:161px;top:742px;width:378px;height:438px;background:var(--white);border:1px solid #c9c9c9;box-shadow:0 2px 8px rgba(0,0,0,.2);padding:8px}
.about-photo{width:100%;height:100%;background:linear-gradient(180deg,#6e6a66,#3d3836)}
.about-title{left:609px;top:770px;font-family:"Montserrat",sans-serif;font-weight:300;font-size:36px;color:var(--ink);letter-spacing:1px}
.about-rule{left:609px;top:824px;width:74px;height:3px;background:var(--blue)}
.about-text{left:609px;top:846px;width:430px;font-size:11.5px;line-height:22px;text-align:justify;color:#555}
.about-text p+p{margin-top:22px}
.about-btn{left:609px;top:1134px;width:156px;height:52px;font-size:13px;line-height:52px}

/* partners */
.partners{left:0;top:1267px;width:1200px;height:287px;background:var(--grey-bg)}
.partner{top:1393px;width:176px;height:99px;background:var(--white);border:1px solid #ddd;display:flex;align-items:center;justify-content:center}

/* services */
.card{border:1px solid var(--line);background:var(--white);top:1695px;height:470px}
.card-photo{width:100%;height:227px}
.card-title{font-family:"Montserrat",sans-serif;font-weight:600;font-size:15px;line-height:27px;color:var(--ink);text-align:center;text-transform:uppercase}
.card-text{font-size:11.5px;line-height:27px;text-align:center;color:#666;padding:0 22px}
.card .btn-outline{width:120px;height:42px;line-height:38px;margin:18px auto 0;font-size:12px}

/* testimonials */
.testi{left:0;top:2301px;width:1200px;height:438px;background:var(--blue)}
.testi-title{left:0;top:2338px;width:1200px;color:var(--white)}
.quote-circle{left:558px;top:2417px;width:84px;height:84px;border:3px solid var(--white);border-radius:50%}
.testi-text{left:290px;top:2518px;width:620px;color:var(--white);font-size:12px;line-height:28px;text-align:center}
.testi-name{left:0;top:2648px;width:1200px;text-align:center;color:var(--white);font-family:"Montserrat",sans-serif;font-weight:600;font-size:15px}
.testi-role{left:0;top:2676px;width:1200px;text-align:center;color:var(--white);font-size:11.5px}

/* media */
.media-sub{left:0;top:2859px;width:1200px;text-align:center;font-size:11.5px;color:#666}
.media-card{top:2922px;width:446px;height:327px;border:1px solid var(--line);background:var(--white)}
.media-photo{width:100%;height:208px}
.media-cap{padding:20px 24px 0;text-align:center;font-size:14px;line-height:29px;color:#444}
.media-cap .hl{color:var(--blue)}

/* footer */
.footer{left:0;top:3310px;width:1200px;height:401px;background:var(--footer)}
.f-brand{left:140px;top:3404px;display:flex;align-items:center;gap:18px}
.f-brand .brand-mark{width:66px;height:66px}
.f-brand .brand-name{color:var(--white);font-size:19px;line-height:24px;letter-spacing:5px}
.socials{left:186px;top:3514px;display:flex;gap:8px}
.socials span{width:36px;height:36px;border:2px solid var(--white);border-radius:50%;display:block}
.f-head{font-family:"Montserrat",sans-serif;font-weight:500;font-size:21px;color:var(--white);letter-spacing:1px}
.f-info{left:505px;top:3405px;width:220px;color:#e6e6e6;font-size:12px;line-height:17px}
.f-info .k{text-transform:uppercase}
.f-info p{margin-bottom:22px}
.form{left:769px;top:3398px;width:282px}
.field{width:282px;height:34px;background:var(--white);margin-top:6px;font-size:11.5px;color:#777;padding:9px 14px}
.field.msg{height:50px}
.submit{width:90px;height:32px;background:var(--blue);color:var(--white);font-family:"Montserrat",sans-serif;font-weight:600;font-size:11px;text-align:center;line-height:32px;margin-top:14px}
.copy{left:0;top:3667px;width:1200px;text-align:center;color:#ddd;font-size:12px}
</style>
</head>
<body>

<div class="abs topline"></div>
<header class="abs nav">
  <nav class="abs nav-links"><span class="active">HOME</span><span>ABOUT</span><span>SERVICES &amp; TESTIMONIALS</span><span>MEDIA &amp; IMPACT</span><span>CONTACT</span></nav>
  <div class="abs brand"><span class="brand-mark"></span><div class="brand-name">Brightwater<br>Civic<br>Advisors</div></div>
</header>

<section class="abs hero" role="img" aria-label="Photo of a speaker presenting at a university event to a seated audience"></section>
<div class="abs hero-title">BRIGHTWATER CIVIC ADVISORS</div>
<div class="abs hero-sub">SED UT PERSPICIATIS UNDE OMNIS ISTE NATUS ERROR SIT VOLUPTATEM</div>

<div class="abs about-frame"></div>
<div class="abs about-photo-wrap"><div class="about-photo" role="img" aria-label="Portrait of the founder, Dana Whitfield"></div></div>
<h2 class="abs about-title">ABOUT ME</h2>
<div class="abs about-rule"></div>
<div class="abs about-text">
  <p>Brightwater Civic Advisors supports nonprofit organizations and educational institutions to carry out their missions to benefit the wider community.</p>
  <p>Founder Dana Whitfield is an educator with a 22-year record of demonstrated achievement and leadership roles in nonprofits and educational institutions. Most recently, she served as Associate Dean of Students in the University and Director of the Campus Community Service Center at Lakeshore University. Dana has designed, implemented, and evaluated community-based learning and leadership training programs that have attained positive outcomes documented by survey results, recognition by outside agencies, and grants awarded for new initiatives and expansions. She has also significantly and consistently…</p>
</div>
<div class="abs btn-solid about-btn">READ MORE</div>

<section class="abs partners"></section>
<h2 class="abs h-section" style="left:0;top:1304px;width:1200px">OUR PARTNERS</h2>
<div class="abs underline" style="left:562px;top:1355px"></div>
<svg class="abs" style="left:48px;top:1420px" width="20" height="46"><polyline points="18,2 3,23 18,44" fill="none" stroke="#cfcfcf" stroke-width="2"/></svg>
<svg class="abs" style="left:1132px;top:1420px" width="20" height="46"><polyline points="2,2 17,23 2,44" fill="none" stroke="#cfcfcf" stroke-width="2"/></svg>
<div class="abs partner" style="left:116px"><svg width="120" height="50"><rect x="0" y="5" width="120" height="40" fill="#9b2a2a"/></svg></div>
<div class="abs partner" style="left:314px"><svg width="60" height="60"><circle cx="30" cy="30" r="26" fill="#2f74b8"/></svg></div>
<div class="abs partner" style="left:512px"><svg width="130" height="44"><rect x="0" y="4" width="130" height="36" fill="#8cc04b"/></svg></div>
<div class="abs partner" style="left:710px"><svg width="130" height="56"><rect x="0" y="0" width="130" height="56" fill="#e07a2e"/></svg></div>
<div class="abs partner" style="left:908px"><svg width="64" height="64"><circle cx="32" cy="32" r="30" fill="#1d2a4d"/></svg></div>

<h2 class="abs h-section" style="left:0;top:1600px;width:1200px">OUR SERVICES</h2>
<div class="abs underline" style="left:562px;top:1651px"></div>

<article class="abs card" style="left:111px;width:322px">
  <div class="card-photo" role="img" aria-label="Group photo of staff members posing with colorful props" style="background:linear-gradient(135deg,#3b2f3a,#7a3048 50%,#2d3a5a)"></div>
  <div class="card-title" style="margin-top:18px">Staff Professional<br>Development</div>
  <div class="card-text" style="margin-top:6px">Dana has supervised, coached, and mentored hundreds of staff members, including professionals personal and professional growth.</div>
  <div class="btn-outline">READ MORE</div>
</article>

<article class="abs card" style="left:440px;width:320px;top:1695px;border-color:#cfcfcf;box-shadow:0 0 6px rgba(0,0,0,.12)">
  <div class="card-title" style="margin-top:22px">Community Partnership<br>Development</div>
  <div class="card-text" style="margin-top:6px">Dana has collaborated with more than 250 non profits, schools, government agencies, &amp; businesses with corporate social responsibility</div>
  <div class="btn-solid" style="width:120px;height:40px;line-height:40px;margin:12px auto 0;font-size:12px">READ MORE</div>
  <div role="img" aria-label="Group photo of smiling students" style="position:absolute;left:0;bottom:0;width:100%;height:227px;background:linear-gradient(160deg,#6a5c58,#2a2628 60%,#8a7f7a)"></div>
</article>

<article class="abs card" style="left:769px;width:320px">
  <div class="card-photo" role="img" aria-label="Audience seated in a gallery space for a facilitated discussion" style="background:linear-gradient(160deg,#c9b79a,#6a5546 55%,#2f2a2a)"></div>
  <div class="card-title" style="margin-top:18px">Group Facilitation &amp;<br>Leadership Training</div>
  <div class="card-text" style="margin-top:6px">Dana has facilitated student groups, experiential learning activities, and dialogues on social justice and privilege, education, and poverty.</div>
  <div class="btn-outline">READ MORE</div>
</article>

<div class="abs btn-outline" style="left:480px;top:2207px;width:240px;height:54px;line-height:50px">VIEW MORE SERVICES</div>

<section class="abs testi"></section>
<h2 class="abs h-section testi-title">TESTIMONIALS</h2>
<div class="abs underline" style="left:562px;top:2389px;background:var(--white)"></div>
<div class="abs quote-circle"><svg width="78" height="78" viewBox="0 0 78 78"><path d="M26 48v-8c0-6 3-10 8-12l2 3c-3 1-5 4-5 7h5v10z M42 48v-8c0-6 3-10 8-12l2 3c-3 1-5 4-5 7h5v10z" fill="#fff"/></svg></div>
<svg class="abs" style="left:166px;top:2446px" width="26" height="120"><polyline points="24,2 2,60 24,118" fill="none" stroke="#8fb8e3" stroke-width="2"/></svg>
<svg class="abs" style="left:1008px;top:2446px" width="26" height="120"><polyline points="2,2 24,60 2,118" fill="none" stroke="#8fb8e3" stroke-width="2"/></svg>
<p class="abs testi-text">Dana has an uncanny ability to combine social change theory and real-world practice in truly compelling ways. For five years at Lakeshore University, I saw first-hand how Dana inspired legions of students, created innovative programs, and transformed relationships with community stakeholders. Best of all, she did it with integrity, smarts, enthusiasm and a warm, infectious spirit</p>
<div class="abs testi-name">Marcus Reyes</div>
<div class="abs testi-role">VP, Chief Content Officer, KRNL Radio</div>

<h2 class="abs h-section" style="left:0;top:2783px;width:1200px">MEDIA &amp; IMPACT</h2>
<div class="abs underline" style="left:562px;top:2834px"></div>
<p class="abs media-sub">Sed ut perspiciatis unde omnis iste natus error sit voluptatem accusantium doloremque laudantium, totam rem aperiam</p>
<article class="abs media-card" style="left:136px">
  <div class="media-photo" role="img" aria-label="Attendees at round tables during a dinner dialogue event" style="background:linear-gradient(160deg,#4a3a34,#221d1d 55%,#6a4a3e)"></div>
  <p class="media-cap"><span class="hl">Attendees listening to a speaker</span> at the Bridgeway Dinner Dialogue event (featured in <span class="hl">March 2018 article</span>)</p>
</article>
<article class="abs media-card" style="left:616px">
  <div class="media-photo" role="img" aria-label="Students performing music at an arts festival" style="background:linear-gradient(160deg,#c7c2bb,#6e6560 55%,#2e2a2a)"></div>
  <p class="media-cap"><span class="hl">Students performing</span> at the third annual Harmon Park Arts Festival (featured in <span class="hl">April 2018 article</span>)</p>
</article>

<footer class="abs footer"></footer>
<div class="abs f-brand"><span class="brand-mark"></span><div class="brand-name">Brightwater<br>Civic<br>Advisors</div></div>
<div class="abs socials"><span></span><span></span><span></span><span></span><span></span></div>
<h3 class="abs f-head" style="left:505px;top:3352px">ADDRESS</h3>
<div class="abs f-info">
  <p><span class="k">Address</span><br>113 S. Lorem Ipsum Dummy<br>Lorem Ipsum</p>
  <p><span class="k">Phone</span><br>(000)-121-1231</p>
  <p><span class="k">Email</span><br>info@brightwatercivic.example/</p>
</div>
<h3 class="abs f-head" style="left:769px;top:3352px">CONTACT FORM</h3>
<form class="abs form">
  <div class="field">Name :</div>
  <div class="field">Email :</div>
  <div class="field">Subject :</div>
  <div class="field msg">Message :</div>
  <div class="submit">SUBMIT</div>
</form>
<p class="abs copy">© Copyright 2019 Brightwater Civic Advisors All right reserved</p>

</body>
</html>
```